Custom Manufacturing Company square space website design

I own a custom manufacturing company that uses precision cutting technology to manufacture project components over a couple industries. We have an industrial CNC router and state of the art edge bander and cut a lot of cabinetry components for cabinet shops, builders, closet companies, ect. We offer design and assembly for any cabinetry or can build cabinets to spec. We also cut components for other industries out of wood, plastics, acryclics, ect. We offer design engineering services, product development protype services. we have a 3D printer farm. We want our communicate trust, dependability, and the value we place on client relationships.

We essentially want a credibility website. Landing page and drops downs for services we offer, capabilites, about us, contact

```html
<!DOCTYPE html>
<html lang="en">
<head>
<meta charset="utf-8">
<title>Northgate CNC</title>
<link href="https://fonts.googleapis.com/css2?family=Oswald:wght@400;500;600&family=Nunito+Sans:wght@400;600;700&display=swap" rel="stylesheet">
<style>
:root{
  --ink:#111111;
  --text:#2a2a2a;
  --muted:#8a8a8a;
  --line:#cfcfcf;
  --paper:#ffffff;
  --soft:#f4f4f4;
  --dark:#1b1b1b;
  --white:#ffffff;
}
*{box-sizing:border-box;margin:0;padding:0}
html,body{width:1200px;height:4494px;overflow:hidden;background:var(--paper)}
body{position:relative;font-family:"Nunito Sans",sans-serif;color:var(--text)}
.abs{position:absolute}
.heading{font-family:"Oswald",sans-serif;font-weight:500;color:var(--ink)}
.btn{position:absolute;display:flex;align-items:center;justify-content:center;font-family:"Oswald",sans-serif;font-weight:500;font-size:15px;color:var(--ink);border:1.5px solid var(--ink);background:transparent}
.btn.solid{background:var(--ink);color:var(--white)}
.btn.light{border-color:var(--white);color:var(--white)}
.section{position:absolute;left:0;width:1200px}
.soft{background:var(--soft)}
.photo{position:absolute}
/* header */
.brand{position:absolute;display:flex;align-items:center;gap:12px;font-weight:700;font-size:22px;letter-spacing:2px;color:var(--ink)}
.brand .mark{width:30px;height:30px;background:var(--ink)}
.topbar{position:absolute;top:30px;font-family:"Oswald",sans-serif;font-size:13px;color:var(--ink);display:flex;align-items:center;gap:6px}
.nav{position:absolute;top:100px;left:440px;display:flex;gap:40px;font-family:"Oswald",sans-serif;font-size:14px;color:var(--ink)}
/* hero */
.hero-title{font-family:"Oswald",sans-serif;font-weight:500;font-size:37px;line-height:44px;color:var(--white)}
.hero-sub{font-size:19px;line-height:28px;color:var(--white)}
/* cards */
.card-cap{position:absolute;width:264px;text-align:center;font-family:"Oswald",sans-serif;font-size:14px;line-height:22px;color:var(--ink)}
.about-text{font-size:13.5px;line-height:29px;color:var(--text)}
.stat-num{font-family:"Oswald",sans-serif;font-weight:500;font-size:38px;color:var(--ink);line-height:1}
.stat-lbl{font-size:15px;color:var(--text)}
.circle{position:absolute;width:158px;height:158px;border-radius:50%;background:var(--white);border:1.5px solid var(--line);display:flex;align-items:center;justify-content:center}
.step{position:absolute;width:200px;text-align:center;font-family:"Oswald",sans-serif;font-size:16px;line-height:20px;color:var(--ink)}
.proj-cap{position:absolute;width:220px;font-family:"Oswald",sans-serif;font-size:13px;line-height:22px;color:var(--ink)}
.navbox{position:absolute;width:37px;height:39px;background:var(--ink);display:flex;align-items:center;justify-content:center}
.cap-card{position:absolute;top:3256px;height:185px;background:var(--white);box-shadow:0 2px 12px rgba(0,0,0,.08);display:flex;flex-direction:column;align-items:center;justify-content:flex-end;padding-bottom:38px;gap:20px;font-family:"Oswald",sans-serif;font-size:16px;color:var(--ink)}
.cap-card.faded{opacity:.35;background:var(--soft);box-shadow:none}
.field{position:absolute;width:291px;border-bottom:1.5px solid var(--line);height:30px;font-size:12px;color:var(--muted)}
.field.req{color:var(--ink)}
.foot-title{font-family:"Oswald",sans-serif;font-size:16px;color:var(--white)}
.foot-link{font-size:13px;color:var(--white);line-height:27px}
.social{position:absolute;top:4438px;width:22px;height:22px;border:1px solid #777}
</style>
</head>
<body>

<!-- header -->
<header class="section" style="top:0;height:143px;background:var(--paper)">
  <div class="brand" style="left:162px;top:56px"><span class="mark"></span>NORTHGATE CNC</div>
  <div class="topbar" style="left:598px">
    <svg width="14" height="14" viewBox="0 0 24 24" fill="none" stroke="#111" stroke-width="2"><path d="M5 3h4l2 5-3 2a11 11 0 0 0 6 6l2-3 5 2v4a2 2 0 0 1-2 2A17 17 0 0 1 3 5a2 2 0 0 1 2-2z"/></svg>(123) 456-7890
  </div>
  <div class="abs" style="left:710px;top:28px;width:1px;height:20px;background:var(--line)"></div>
  <div class="topbar" style="left:727px">
    <svg width="14" height="12" viewBox="0 0 24 18" fill="none" stroke="#111" stroke-width="2"><rect x="1" y="1" width="22" height="16"/><path d="M1 1l11 9 11-9"/></svg>info@northgatecnc.com
  </div>
  <div class="abs" style="left:890px;top:28px;width:1px;height:20px;background:var(--line)"></div>
  <div class="abs" style="left:912px;top:30px;width:128px;height:18px;border-bottom:1px solid var(--line);font-size:11px;color:var(--muted)">Search...
    <svg class="abs" style="right:2px;top:3px" width="11" height="11" viewBox="0 0 24 24" fill="none" stroke="#111" stroke-width="3"><circle cx="10" cy="10" r="7"/><path d="M15 15l7 7"/></svg>
  </div>
  <div class="abs" style="left:440px;top:70px;width:600px;height:1px;background:var(--line)"></div>
  <nav class="nav"><span>Home</span><span>About Us</span><span>Services ▾</span><span>Capabilities</span><span>CONTACT US</span></nav>
  <div class="btn" style="left:884px;top:89px;width:155px;height:42px">Request A Quote</div>
</header>

<!-- hero -->
<section class="section" style="top:143px;height:508px">
  <div class="photo" role="img" aria-label="Machinist operating a CNC milling spindle over a workpiece" style="inset:0;background:linear-gradient(100deg,#1a2430 0%,#2b3a48 45%,#55606a 65%,#2a3440 100%)"></div>
  <div class="abs" style="left:162px;top:122px;width:560px">
    <h1 class="hero-title">Looking For A Reliable Supplier<br>For CNC Machining, Production<br>Machining Services?</h1>
  </div>
  <p class="abs hero-sub" style="left:162px;top:262px;width:560px">Providing high precision short run machining services<br>for local industry in Western New York.</p>
  <div class="btn light" style="left:162px;top:330px;width:164px;height:47px">Request A Quote</div>
</section>

<!-- what we do -->
<section class="section" style="top:651px;height:483px">
  <h2 class="heading abs" style="left:0;width:1200px;top:82px;text-align:center;font-size:30px">What We Do</h2>
  <div class="photo" role="img" aria-label="Cabinet design drawings on a computer monitor" style="left:160px;top:151px;width:264px;height:161px;background:linear-gradient(135deg,#d9d6cf,#9a8f80)"></div>
  <div class="photo" role="img" aria-label="Laser cutter cutting sheet material" style="left:467px;top:151px;width:264px;height:161px;background:linear-gradient(135deg,#2a2a22,#6b6a40)"></div>
  <div class="photo" role="img" aria-label="Engineer working on product prototype with a machine" style="left:776px;top:151px;width:264px;height:161px;background:linear-gradient(135deg,#2a3e6a,#6f7c9a)"></div>
  <p class="card-cap" style="left:160px;top:343px">We Offer Design And Assembly For Any<br>Cabinetry Or Can Build Cabinets To<br>Specifications.</p>
  <p class="card-cap" style="left:467px;top:343px">We Also Cut Components For Other<br>Industries Out Of Wood, Plastics, Acrylics,<br>Etc.</p>
  <p class="card-cap" style="left:776px;top:343px">We Offer Design Engineering Services,<br>Product Development Protype Services.</p>
</section>

<!-- about -->
<section class="section soft" style="top:1134px;height:561px">
  <h2 class="heading abs" style="left:162px;top:94px;font-size:31px">About Us</h2>
  <p class="abs about-text" style="left:162px;top:160px;width:430px">Lorem ipsum dolor sit amet, consectetur adipiscing elit. Etiam suscipit lorem eget ligula tincidunt pharetra. Sed aliquam lacus et dolor tempus mollis. Etiam luctus, metus eget lobortis porttitor, arcu orci bibendum dolor, ut accumsan lacus nibh et nisi. Curabitur et pharetra orci. Sed vulputate erat risus. Sed lobortis nunc eleifend ornare ultrices. Mauris eget justo nisi. Nulla ultrices commodo orci ac vulputate. Nunc at leo quis elit tincidunt placerat. Nunc lacinia rutrum varius.</p>
  <div class="btn solid" style="left:162px;top:416px;width:134px;height:42px">Read More</div>
  <div class="photo" role="img" aria-label="Operator in hard hat at a CNC machine control panel" style="left:644px;top:96px;width:355px;height:369px;background:linear-gradient(90deg,#cfd2d4 0%,#b9bec2 10%,#2c4f8a 25%,#3a5f9c 70%,#2a3a5a 100%)"></div>
</section>

<!-- stats -->
<section class="section" style="top:1695px;height:298px">
  <div class="abs" style="left:162px;top:90px">
    <svg width="48" height="42" viewBox="0 0 48 42" fill="none" stroke="#111" stroke-width="2"><rect x="2" y="10" width="44" height="30" rx="3"/><path d="M16 10V4h16v6M2 22h44"/><rect x="20" y="19" width="8" height="7"/></svg>
    <div class="stat-num" style="margin-top:20px">20+</div><div class="stat-lbl" style="margin-top:10px">Years of Experience</div>
  </div>
  <div class="abs" style="left:396px;top:90px">
    <svg width="44" height="42" viewBox="0 0 44 42" fill="none" stroke="#111" stroke-width="2"><path d="M4 2v40M4 4h36v22H4"/><path d="M4 11h36M4 18h36"/></svg>
    <div class="stat-num" style="margin-top:20px">100%</div><div class="stat-lbl" style="margin-top:10px">Made in America</div>
  </div>
  <div class="abs" style="left:630px;top:90px">
    <svg width="46" height="46" viewBox="0 0 46 46" fill="none" stroke="#111" stroke-width="2"><circle cx="23" cy="23" r="21"/><ellipse cx="23" cy="23" rx="9" ry="21"/><path d="M2 23h42M6 12h34M6 34h34"/></svg>
    <div class="stat-num" style="margin-top:16px">Global</div><div class="stat-lbl" style="margin-top:10px">Servicimg the Globe</div>
  </div>
  <div class="abs" style="left:863px;top:90px">
    <svg width="46" height="42" viewBox="0 0 46 42" fill="none" stroke="#111" stroke-width="2"><circle cx="23" cy="15" r="12"/><circle cx="23" cy="15" r="6"/><path d="M15 25l-4 15 6-3 4 5 2-14M31 25l4 15-6-3-4 5"/></svg>
    <div class="abs" style="left:0;top:62px;width:72px;height:30px;border:2px solid #111"></div>
    <div class="stat-lbl" style="margin-top:54px">Industry Standatrds Met</div>
  </div>
</section>

<!-- process -->
<section class="section soft" style="top:1993px;height:546px">
  <h2 class="heading abs" style="left:0;width:1200px;top:84px;text-align:center;font-size:30px">Our Process</h2>
  <div class="circle" style="left:162px;top:162px"><svg width="66" height="66" viewBox="0 0 66 66" fill="none" stroke="#111" stroke-width="2"><path d="M14 30a19 19 0 0 1 38 0M10 30h46v5H10z"/><path d="M33 11v12"/><circle cx="33" cy="48" r="8"/><path d="M20 48h5M41 48h5M33 36v4M33 56v4M24 40l3 3M39 53l3 3M42 40l-3 3M24 56l3-3"/></svg></div>
  <div class="circle" style="left:401px;top:162px"><svg width="70" height="66" viewBox="0 0 70 66" fill="none" stroke="#111" stroke-width="2"><path d="M35 6l30 14-30 14L5 20z"/><path d="M5 32l30 14 30-14M5 44l30 14 30-14"/></svg></div>
  <div class="circle" style="left:640px;top:162px"><svg width="70" height="66" viewBox="0 0 70 66" fill="none" stroke="#111" stroke-width="2"><rect x="12" y="6" width="46" height="8"/><rect x="28" y="14" width="14" height="14"/><path d="M35 28v14M30 42h10"/><path d="M6 52h58v6H6z"/></svg></div>
  <div class="circle" style="left:880px;top:162px"><svg width="74" height="60" viewBox="0 0 74 60" fill="none" stroke="#111" stroke-width="2"><path d="M20 14h32v28H20zM52 24h10l8 10v8H52"/><circle cx="30" cy="46" r="5"/><circle cx="60" cy="46" r="5"/><path d="M2 20h12M6 28h10M2 36h12"/></svg></div>
  <svg class="abs" style="left:340px;top:230px" width="40" height="20" viewBox="0 0 40 20" fill="none" stroke-width="3"><path d="M2 3l7 7-7 7" stroke="#222"/><path d="M14 3l7 7-7 7" stroke="#777"/><path d="M26 3l7 7-7 7" stroke="#bbb"/></svg>
  <svg class="abs" style="left:579px;top:230px" width="40" height="20" viewBox="0 0 40 20" fill="none" stroke-width="3"><path d="M2 3l7 7-7 7" stroke="#222"/><path d="M14 3l7 7-7 7" stroke="#777"/><path d="M26 3l7 7-7 7" stroke="#bbb"/></svg>
  <svg class="abs" style="left:818px;top:230px" width="40" height="20" viewBox="0 0 40 20" fill="none" stroke-width="3"><path d="M2 3l7 7-7 7" stroke="#222"/><path d="M14 3l7 7-7 7" stroke="#777"/><path d="M26 3l7 7-7 7" stroke="#bbb"/></svg>
  <p class="step" style="left:141px;top:343px">Application<br>Engineering</p>
  <p class="step" style="left:380px;top:343px">Material<br>Selection</p>
  <p class="step" style="left:619px;top:343px">Part Fabrication</p>
  <p class="step" style="left:859px;top:343px">Delivery</p>
  <div class="btn" style="left:532px;top:415px;width:136px;height:42px">Get Started</div>
</section>

<!-- recent projects -->
<section class="section" style="top:2539px;height:579px">
  <h2 class="heading abs" style="left:0;width:1200px;top:84px;text-align:center;font-size:30px">Recent Projects</h2>
  <div class="photo" role="img" aria-label="Worker grinding metal with sparks" style="left:160px;top:162px;width:264px;height:204px;background:linear-gradient(135deg,#3a2e24,#8a7a66)"></div>
  <div class="photo" role="img" aria-label="Operator using a tablet beside a milling machine" style="left:467px;top:162px;width:264px;height:204px;background:linear-gradient(135deg,#5a5a5a,#b8b0a4)"></div>
  <div class="photo" role="img" aria-label="Welder working on a metal frame" style="left:776px;top:162px;width:264px;height:204px;background:linear-gradient(135deg,#1e1e1e,#6a5648)"></div>
  <p class="proj-cap" style="left:164px;top:380px">Lorem Ipsum Dolor Sit Consectetur<br>Adipiscing Elit. Etiam Suscipit Lorem.</p>
  <p class="proj-cap" style="left:471px;top:380px">Lorem Ipsum Dolor Sit Consectetur<br>Adipiscing Elit. Etiam Suscipit Lorem.</p>
  <p class="proj-cap" style="left:780px;top:380px">Lorem Ipsum Dolor Sit Consectetur<br>Adipiscing Elit. Etiam Suscipit Lorem.</p>
  <svg class="abs" style="left:398px;top:397px" width="18" height="14" viewBox="0 0 18 14" fill="none" stroke="#111" stroke-width="2"><path d="M0 7h16M10 1l6 6-6 6"/></svg>
  <svg class="abs" style="left:705px;top:397px" width="18" height="14" viewBox="0 0 18 14" fill="none" stroke="#111" stroke-width="2"><path d="M0 7h16M10 1l6 6-6 6"/></svg>
  <svg class="abs" style="left:1014px;top:397px" width="18" height="14" viewBox="0 0 18 14" fill="none" stroke="#111" stroke-width="2"><path d="M0 7h16M10 1l6 6-6 6"/></svg>
  <div class="navbox" style="left:101px;top:246px"><svg width="16" height="12" viewBox="0 0 16 12" fill="none" stroke="#fff" stroke-width="1.5"><path d="M16 6H1M6 1L1 6l5 5"/></svg></div>
  <div class="navbox" style="left:1062px;top:246px"><svg width="16" height="12" viewBox="0 0 16 12" fill="none" stroke="#fff" stroke-width="1.5"><path d="M0 6h15M10 1l5 5-5 5"/></svg></div>
  <div class="btn" style="left:535px;top:454px;width:128px;height:40px">View All</div>
</section>

<!-- capabilities -->
<section class="section soft" style="top:3118px;height:480px">
  <h2 class="heading abs" style="left:0;width:1200px;top:78px;text-align:center;font-size:30px">Our Capabilites</h2>
</section>
<div class="cap-card faded" style="left:0;width:181px"><svg width="40" height="56" viewBox="0 0 40 56" fill="none" stroke="#111" stroke-width="2"><path d="M4 6h32v6H4zM14 12h12v8H14zM20 20v32"/></svg>Reaming</div>
<div class="cap-card" style="left:204px;width:181px"><svg width="56" height="56" viewBox="0 0 56 56" fill="none" stroke="#111" stroke-width="2"><path d="M10 4h36v8H10zM20 12h16v12H20zM28 24v10M6 42h44v8H6z"/><path d="M22 38l6-4 6 4"/></svg>Parting/Cutting</div>
<div class="cap-card" style="left:406px;width:182px"><svg width="56" height="56" viewBox="0 0 56 56" fill="none" stroke="#111" stroke-width="2"><circle cx="28" cy="30" r="16"/><circle cx="28" cy="30" r="5"/><path d="M14 8l10 12M6 50h44"/></svg>Facing</div>
<div class="cap-card" style="left:610px;width:182px"><svg width="56" height="56" viewBox="0 0 56 56" fill="none" stroke="#111" stroke-width="2"><path d="M18 4v36M14 40h30v8H14zM6 48h44M30 28h12v12H30z"/></svg>Turning</div>
<div class="cap-card" style="left:814px;width:182px"><svg width="56" height="56" viewBox="0 0 56 56" fill="none" stroke="#111" stroke-width="2"><path d="M20 6l10 10-8 8-10-10zM26 20l6 12M22 36h20v14H22zM8 50h44"/><circle cx="32" cy="43" r="3"/></svg>Boring</div>
<div class="cap-card faded" style="left:1017px;width:183px"><svg width="56" height="56" viewBox="0 0 56 56" fill="none" stroke="#111" stroke-width="2"><path d="M24 4v12M16 16h16v8H16zM24 24v14M6 38h46v14H6zM6 45h46"/></svg>Drilling</div>
<div class="navbox" style="left:122px;top:3331px"><svg width="16" height="12" viewBox="0 0 16 12" fill="none" stroke="#fff" stroke-width="1.5"><path d="M16 6H1M6 1L1 6l5 5"/></svg></div>
<div class="navbox" style="left:1039px;top:3331px"><svg width="16" height="12" viewBox="0 0 16 12" fill="none" stroke="#fff" stroke-width="1.5"><path d="M0 6h15M10 1l5 5-5 5"/></svg></div>
<div class="btn" style="left:535px;top:3476px;width:128px;height:40px">Contact Us</div>

<!-- contact -->
<section class="section" style="top:3598px;height:551px">
  <h2 class="heading abs" style="left:0;width:1200px;top:82px;text-align:center;font-size:30px">Contact Us</h2>
</section>
<div class="field req" style="left:298px;top:3762px">First Name*</div>
<div class="field" style="left:610px;top:3762px">Last Name*</div>
<div class="field" style="left:298px;top:3838px">Phone Number*</div>
<div class="field" style="left:610px;top:3838px">Postal Code*</div>
<div class="field" style="left:298px;top:3915px;width:604px">Message*</div>
<div class="btn" style="left:549px;top:4016px;width:102px;height:42px">Submit</div>

<!-- footer -->
<footer class="section" style="top:4149px;height:345px;background:var(--dark)">
  <p class="abs foot-title" style="left:162px;top:72px">Quick Links</p>
  <div class="abs" style="left:162px;top:105px">
    <p class="foot-link">Home</p><p class="foot-link">About Us</p><p class="foot-link">Services</p><p class="foot-link">Capabilities</p><p class="foot-link">Contact Us</p>
  </div>
  <div class="brand" style="left:428px;top:174px;color:var(--white)"><span class="mark" style="background:var(--white)"></span>NORTHGATE CNC</div>
  <p class="abs foot-title" style="left:818px;top:72px">Contact Details</p>
  <svg class="abs" style="left:818px;top:108px" width="12" height="16" viewBox="0 0 12 16" fill="#fff"><path d="M6 0a6 6 0 0 1 6 6c0 4-6 10-6 10S0 10 0 6a6 6 0 0 1 6-6zm0 3.5a2.5 2.5 0 1 0 0 5 2.5 2.5 0 0 0 0-5z"/></svg>
  <p class="abs foot-link" style="left:848px;top:102px;line-height:20px">123, Building Name, Street<br>City, State XY 123456</p>
  <svg class="abs" style="left:818px;top:163px" width="14" height="14" viewBox="0 0 24 24" fill="#fff"><path d="M5 2h4l2 5-3 2a11 11 0 0 0 6 6l2-3 5 2v4a2 2 0 0 1-2 2A17 17 0 0 1 3 4a2 2 0 0 1 2-2z"/></svg>
  <p class="abs foot-link" style="left:848px;top:156px">(123) 456-7890</p>
  <svg class="abs" style="left:818px;top:205px" width="15" height="11" viewBox="0 0 24 18" fill="#fff"><path d="M0 0h24v18H0z"/><path d="M0 0l12 9L24 0" stroke="#1b1b1b" stroke-width="2" fill="none"/></svg>
  <p class="abs foot-link" style="left:848px;top:196px">info@northgatecnc.com</p>
  <div class="abs" style="left:162px;top:268px;width:876px;height:1px;background:#3a3a3a"></div>
  <p class="abs" style="left:162px;top:294px;font-size:13px;color:var(--white)">© 2023 Northgate CNC. All Rights Reserved.</p>
</footer>
<div class="social" style="left:900px"></div>
<div class="social" style="left:938px"></div>
<div class="social" style="left:976px"></div>
<div class="social" style="left:1014px"></div>

</body>
</html>
```